Super elegant, crisp & clean Business card design required

We recently upgraded our branding - which is on our website - talvendoraphoto.com

I would like a simple, yet elegant, clean business card design please.

The font of my logo is Cinzel - and because of the natural colour - it's best to have this on a black background.

I would like to have the back of the business card - with simply my logo.

PLEASE DO NOT SUBMIT A COMPLICATED / UNCLEAN DESIGN

Industry/Entity Type

Business

Contact Information for Business Card

Talven Doroshko Photography

Font styles to use
Other font styles liked:
• Cinzel

Requirements
Must have
• A backpage with nothing but my logo
• Simple design - stands out
Should not have
• Colour that dont align with my logo
• Over complicated '/ non symmetrical design

```html
<!DOCTYPE html>
<html lang="en">
<head>
<meta charset="utf-8">
<title>Talven Doroshko Photography – Business Card</title>
<link href="https://fonts.googleapis.com/css2?family=Cinzel:wght@400;500&family=Arimo:wght@400&display=swap" rel="stylesheet">
<style>
  :root {
    --taupe: #857761;
    --taupe-light: #948670;
    --paper: #ffffff;
    --ink: #1f1f1f;
    --backdrop: #ebe6de;
    --card-shadow: rgba(40, 30, 20, 0.22);
  }
  * { margin: 0; padding: 0; box-sizing: border-box; }
  html, body {
    width: 1200px; height: 892px; overflow: hidden;
    background: var(--backdrop);
  }
  .canvas { position: relative; width: 1200px; height: 892px; }

  .card {
    position: absolute;
    width: 580px; height: 331px;
    border-radius: 4px;
    box-shadow: 0 10px 28px var(--card-shadow);
    overflow: hidden;
  }

  /* Back of card: name only */
  .card-back {
    left: 560px; top: 70px;
    background: linear-gradient(135deg, var(--taupe) 0%, var(--taupe-light) 100%);
    display: flex; align-items: center; justify-content: center;
  }

  .wordmark {
    font-family: 'Cinzel', serif;
    font-weight: 400;
    color: var(--paper);
    text-align: center;
    line-height: 1.3;
  }
  .wordmark .wordmark-name { display: block; font-size: 34px; letter-spacing: 1px; }
  .wordmark .wordmark-trade { display: block; font-size: 15px; letter-spacing: 11px; margin-left: 11px; }

  /* Front of card */
  .card-front {
    left: 70px; top: 480px;
    display: flex;
    background: var(--paper);
  }
  .front-brand {
    width: 232px; height: 100%;
    background: linear-gradient(135deg, var(--taupe) 0%, var(--taupe-light) 100%);
    display: flex; align-items: center; justify-content: center;
  }
  .front-brand .wordmark-name { font-size: 19px; letter-spacing: 0.5px; }
  .front-brand .wordmark-trade { font-size: 9px; letter-spacing: 6px; margin-left: 6px; }

  .contact {
    flex: 1;
    padding: 38px 0 0 26px;
    list-style: none;
  }
  .contact-row {
    display: flex; align-items: center;
    height: 62px;
  }
  .contact-icon {
    width: 30px; height: 30px; flex: none;
    background: var(--taupe);
    border-radius: 3px;
    display: flex; align-items: center; justify-content: center;
    margin-right: 22px;
  }
  .contact-icon svg { width: 18px; height: 18px; }
  .contact-text {
    font-family: 'Arimo', sans-serif;
    font-size: 16px;
    letter-spacing: 2px;
    color: var(--ink);
  }
  .contact-name {
    font-family: 'Cinzel', serif;
    font-size: 19px;
    letter-spacing: 3px;
    color: var(--ink);
    line-height: 1.05;
  }
  .contact-role {
    display: block;
    font-size: 12px;
    letter-spacing: 2px;
  }
</style>
</head>
<body>
<main class="canvas">

  <section class="card card-back" aria-label="Business card back">
    <p class="wordmark">
      <span class="wordmark-name">Talven Doroshko</span>
      <span class="wordmark-trade">Photography</span>
    </p>
  </section>

  <section class="card card-front" aria-label="Business card front">
    <div class="front-brand">
      <p class="wordmark">
        <span class="wordmark-name">Talven Doroshko</span>
        <span class="wordmark-trade">Photography</span>
      </p>
    </div>

    <ul class="contact">
      <li class="contact-row">
        <span class="contact-icon">
          <svg viewBox="0 0 18 18" fill="#fff"><circle cx="9" cy="6" r="3.4"/><path d="M2.5 17c0-4 2.9-6.2 6.5-6.2s6.5 2.2 6.5 6.2z"/></svg>
        </span>
        <p class="contact-name">Talven Doroshko<span class="contact-role">Owner</span></p>
      </li>
      <li class="contact-row">
        <span class="contact-icon">
          <svg viewBox="0 0 18 18" fill="none" stroke="#fff" stroke-width="1.6"><rect x="5" y="1.5" width="8" height="15" rx="1.5"/><line x1="8" y1="14" x2="10" y2="14"/></svg>
        </span>
        <p class="contact-text">07946218305</p>
      </li>
      <li class="contact-row">
        <span class="contact-icon">
          <svg viewBox="0 0 18 18" fill="none" stroke="#fff" stroke-width="1.5"><circle cx="9" cy="9" r="7"/><ellipse cx="9" cy="9" rx="3" ry="7"/><line x1="2" y1="9" x2="16" y2="9"/></svg>
        </span>
        <p class="contact-text">www.talvendoraphoto.com</p>
      </li>
      <li class="contact-row">
        <span class="contact-icon">
          <svg viewBox="0 0 18 18" fill="none" stroke="#fff" stroke-width="1.5"><rect x="2" y="4" width="14" height="10" rx="1"/><path d="M2 4.5l7 5.5 7-5.5"/></svg>
        </span>
        <p class="contact-text">info@talvendoraphoto.com</p>
      </li>
    </ul>
  </section>

</main>
</body>
</html>
```